Private Investment Firm Needs PowerPoint Presentation Template

Design PowerPoint template, take Pinebrook-submitted rough presentation draft, and drop it into new template. See attached Project Brief file for more detail.
Updates

Some decent designs have been submitted but they seem to lack the understanding of our target markets. I am hopeful that more time and feedback will result in better results.

Target Market(s)

Private company owners and intermediaries.

Font styles to use
Serif

Colors
3176b5

Requirements
Must have
• See attached Project Brief.
Nice to have
Should not have
• No B2C fluff--this is a B2B project.

```html
<!DOCTYPE html>
<html lang="en">
<head>
<meta charset="utf-8">
<title>Pinebrook Capital – Presentation Template</title>
<link rel="stylesheet" href="https://fonts.googleapis.com/css2?family=Cinzel:wght@500;600&family=Montserrat:wght@300;400;600;700&display=swap">
<style>
  :root {
    --brand-blue: #1a6fc0;
    --brand-blue-deep: #1565b0;
    --brand-blue-light: #2a8ad8;
    --band-gray: #6f6f6f;
    --text-gray: #555a60;
    --text-dark: #2f3338;
    --page-bg: #e9e9e9;
    --slide-bg: #ffffff;
  }
  * { box-sizing: border-box; margin: 0; padding: 0; }
  html, body { width: 1200px; height: 1200px; overflow: hidden; }
  body { background: var(--page-bg); font-family: "Montserrat", sans-serif; position: relative; }

  .slide {
    position: absolute; left: 100px; width: 1000px; height: 563px;
    background: linear-gradient(160deg, #ffffff 0%, #f3f4f6 100%);
    box-shadow: 0 6px 14px rgba(0,0,0,0.25);
    overflow: hidden;
  }
  .slide--title { top: 26px; }
  .slide--intro { top: 612px; }
  .slide svg.shapes { position: absolute; inset: 0; }

  .title-block { position: absolute; left: 80px; width: 440px; top: 118px; text-align: center; }
  .title-main {
    font-family: "Cinzel", serif; font-weight: 600; color: var(--brand-blue-deep);
    font-size: 39px; line-height: 43px; letter-spacing: 0.5px;
  }
  .title-sub {
    margin-top: 58px; font-weight: 300; font-size: 15px; line-height: 21px; color: var(--text-gray);
  }
  .title-sub strong { font-weight: 600; color: var(--brand-blue); }

  .brand-name {
    position: absolute; left: 0; width: 600px; top: 440px; text-align: center;
    font-family: "Cinzel", serif; font-weight: 500; font-size: 22px; letter-spacing: 3px; color: var(--brand-blue-deep);
  }
  .brand-name .dot {
    display: inline-block; width: 14px; height: 14px; border-radius: 50%;
    background: var(--brand-blue-deep); margin-right: 10px; vertical-align: 1px;
  }
  .site-url { position: absolute; left: 0; width: 600px; top: 507px; text-align: center; font-size: 21px; color: var(--text-dark); }
  .site-url b { font-weight: 700; color: var(--brand-blue); }

  .intro-heading {
    position: absolute; left: 0; width: 1022px; top: 52px; text-align: center;
    font-weight: 700; font-size: 31px; letter-spacing: 1px; color: var(--brand-blue-deep);
  }
  .intro-rule { position: absolute; left: 486px; top: 94px; width: 50px; height: 4px; background: var(--brand-blue-deep); }
  .intro-lead {
    position: absolute; left: 0; width: 1022px; top: 127px; text-align: center;
    font-weight: 400; font-size: 31px; line-height: 35px; color: var(--text-gray);
  }
  .points { position: absolute; list-style: none; width: 320px; font-size: 13px; line-height: 15px; color: var(--text-dark); }
  .points li { position: relative; padding-left: 16px; margin-bottom: 14px; }
  .points li::before {
    content: ""; position: absolute; left: 0; top: 5px; width: 5px; height: 5px; border-radius: 50%; background: var(--brand-blue);
  }
  .points--a { left: 140px; top: 250px; }
  .points--b { left: 532px; top: 250px; }
  .points--c { left: 140px; top: 349px; }
  .points--d { left: 532px; top: 349px; }
  .points li.justified { text-align: justify; }

  .brand-faint {
    position: absolute; left: 0; width: 1022px; top: 466px; text-align: center;
    font-family: "Cinzel", serif; font-weight: 500; font-size: 15px; letter-spacing: 2px; color: #dfe3e8;
  }
  .slide--intro .site-url { width: 1022px; top: 514px; font-size: 16px; }
</style>
</head>
<body>

<section class="slide slide--title">
  <svg class="shapes" width="1000" height="563" viewBox="0 0 1000 563">
    <defs>
      <linearGradient id="cityTone" x1="0" y1="0" x2="0" y2="1">
        <stop offset="0" stop-color="#5f87b4"/>
        <stop offset="0.45" stop-color="#8e95a0"/>
        <stop offset="0.8" stop-color="#7a5a3c"/>
        <stop offset="1" stop-color="#3e3226"/>
      </linearGradient>
    </defs>
    <polygon points="0,0 100,0 0,415" fill="var(--brand-blue-deep)"/>
    <polygon points="635,0 1000,0 1000,563 456,563" fill="url(#cityTone)" role="img" aria-label="Evening city skyline with lit office towers and a busy avenue"/>
  </svg>
  <div class="title-block">
    <h1 class="title-main">Introduction to<br>Non-Control Capital</h1>
    <p class="title-sub">The Lower Middle Market Private Company Strategy for Raising Capital While <strong>Maintaining Business Control</strong></p>
  </div>
  <div class="brand-name"><span class="dot"></span>PINEBROOK CAPITAL</div>
  <div class="site-url">www.<b>pinebrookcapital</b>.com</div>
</section>

<section class="slide slide--intro">
  <svg class="shapes" width="1000" height="563" viewBox="0 0 1000 563">
    <defs>
      <linearGradient id="blueBand" x1="0" y1="0" x2="1" y2="1">
        <stop offset="0" stop-color="var(--brand-blue-deep)"/>
        <stop offset="1" stop-color="var(--brand-blue-light)"/>
      </linearGradient>
    </defs>
    <polygon points="0,0 100,0 0,500" fill="var(--band-gray)"/>
    <polygon points="871,0 1000,0 1000,563 868,563 957,278" fill="url(#blueBand)"/>
  </svg>
  <h2 class="intro-heading">INTRODUCTION</h2>
  <div class="intro-rule"></div>
  <p class="intro-lead">Private company owners have traditionally<br>considered two capital raising options</p>

  <ul class="points points--a">
    <li>Borrow from a local bank, or</li>
    <li>Sell most or all of the company to a change-of-control investor (aka Buyout firm)</li>
  </ul>
  <ul class="points points--b">
    <li>Non-Control Capital is not appropriate for every private company owner but neither is a Change-of-Control sale</li>
  </ul>
  <ul class="points points--c">
    <li class="justified">An alternative most have not considered is the raising of Non-Control Capital, or capital that is invested into the business yet allows those same owners to retain controlling interest in their company</li>
  </ul>
  <ul class="points points--d">
    <li class="justified">The key is to determine what the business and owners require, and then partner with an investor best aligned with those needs so that long-term company growth, and personal goals, can both be achieved</li>
  </ul>

  <div class="brand-faint">PINEBROOK CAPITAL</div>
  <div class="site-url">www.<b>pinebrookcapital</b>.com</div>
</section>

</body>
</html>
```